Seeking funky, innovative business cards

I am looking to refresh our current business cards to something more engaging, visual and impactful. We are a management consultancy firm, see website (www.larkstone-partners.com.au). I've included our colour scheme, sample of the slides we use and our old business cards. We would like our cards to have icons. The card should display:- Name- Title- Mobile number- Address- Email address- Website - Company logo- Our purpose statement "We shape the finest places anywhere to thrive"

Contact Information for Business Card

Brennan Ulfsson
Consultant
0468 927 341
Level 3, 218 Wexley Street, Melbourne 3000
brennan@larkstone-partners.com.au
www.larkstone-partners.com.au

Purpose statement "We shape the finest places anywhere to thrive"
LOGO available in google images

Font styles to use
Other font styles liked:
• Open Sans Light, Bebas Neue (open to other cool foints)

Colors
ffc214
5c5c5c
f5f5f5
fefefe

Requirements
Must have
• - Name
• - Title
• - Mobile number
• - Address
• - Email address
• - Website
• - Company logo
• - Our purpose statement "We shape the finest places anywhere to thrive"
Nice to have
• - Icons
• - Colour (see our colour scheme"

```html
<!DOCTYPE html>
<html lang="en">
<head>
<meta charset="utf-8">
<title>Larkstone Partners — Business Cards</title>
<link rel="stylesheet" href="https://fonts.googleapis.com/css2?family=Bebas+Neue&family=Open+Sans:wght@300;400;600&display=swap">
<style>
  :root {
    --stage: #4b4b4b;
    --brand-yellow: #e6b017;
    --accent-yellow: #f0b41a;
    --ink: #5c5c5c;
    --card-white: #f1f1f1;
    --white: #fefefe;
    --edge: #5a5a5a;
  }
  * { margin: 0; padding: 0; box-sizing: border-box; }
  html, body {
    width: 1200px; height: 829px; overflow: hidden;
    background: var(--stage);
    font-family: "Open Sans", sans-serif;
  }
  .canvas { position: relative; width: 1200px; height: 829px; }

  .card {
    position: absolute; top: 283px;
    width: 485px; height: 277px;
    overflow: hidden;
  }

  /* Front */
  .card--front { left: 82px; background: var(--brand-yellow); }
  .front__brand {
    position: absolute; left: 0; right: 0; top: 112px;
    display: flex; justify-content: center; align-items: center; gap: 10px;
    color: var(--white);
    font-weight: 300; font-size: 36px; letter-spacing: -0.5px;
  }
  .brand__dot {
    width: 10px; height: 10px; border-radius: 50%;
    background: var(--white);
  }
  .front__purpose {
    position: absolute; left: 0; right: 0; top: 229px;
    text-align: center;
    color: var(--white);
    font-weight: 600; font-size: 11.5px; letter-spacing: 0.1px;
    text-transform: uppercase;
  }

  /* Back */
  .card--back { left: 628px; background: var(--card-white); }
  .card--back::after {
    content: ""; position: absolute; left: 0; right: 0; bottom: 0;
    height: 8px; background: var(--edge);
  }
  .back__brand {
    position: absolute; left: 20px; width: 215px; top: 124px;
    display: flex; justify-content: center; align-items: center; gap: 7px;
    color: var(--ink);
    font-weight: 400; font-size: 21px; letter-spacing: -0.4px;
  }
  .back__brand .brand__dot { width: 7px; height: 7px; background: var(--accent-yellow); }
  .back__divider {
    position: absolute; left: 242px; top: 77px;
    width: 1.5px; height: 123px; background: var(--ink);
  }
  .contact { position: absolute; left: 267px; top: 76px; color: var(--ink); }
  .contact__name {
    font-family: "Bebas Neue", sans-serif;
    font-size: 24px; line-height: 1; color: var(--accent-yellow);
    letter-spacing: 0.2px;
  }
  .contact__title { font-weight: 300; font-size: 12px; line-height: 15px; }
  .contact__address {
    margin-top: 11px; font-weight: 300; font-size: 12px; line-height: 14px;
    font-style: normal;
  }
  .contact__list { list-style: none; margin-top: 10px; }
  .contact__item {
    display: flex; align-items: center; gap: 7px;
    font-weight: 300; font-size: 11.2px; line-height: 14px;
  }
  .contact__icon { width: 9px; height: 9px; flex: none; }
</style>
</head>
<body>
<main class="canvas">

  <section class="card card--front" aria-label="Card front">
    <div class="front__brand"><span class="brand__dot"></span>Larkstone Partners</div>
    <p class="front__purpose">We shape the finest places anywhere to thrive</p>
  </section>

  <section class="card card--back" aria-label="Card back">
    <div class="back__brand"><span class="brand__dot"></span>Larkstone Partners</div>
    <div class="back__divider"></div>
    <div class="contact">
      <h1 class="contact__name">Brennan Ulfsson</h1>
      <p class="contact__title">Consultant</p>
      <address class="contact__address">Level 7, 218 Wexley Street<br>Melbourne 3012</address>
      <ul class="contact__list">
        <li class="contact__item">
          <svg class="contact__icon" viewBox="0 0 10 10" aria-hidden="true"><path d="M2 1 L4 1 L4.6 3 L3.4 3.8 Q4.4 5.8 6.2 6.6 L7 5.4 L9 6 L9 8 Q8.5 9 7.5 9 Q1 8.5 1 2.5 Q1 1.5 2 1Z" fill="var(--accent-yellow)"/></svg>
          0468 927 341
        </li>
        <li class="contact__item">
          <svg class="contact__icon" viewBox="0 0 10 10" aria-hidden="true"><rect x="0.8" y="2" width="8.4" height="6" fill="none" stroke="var(--accent-yellow)" stroke-width="1"/><path d="M0.8 2 L5 5.4 L9.2 2" fill="none" stroke="var(--accent-yellow)" stroke-width="1"/></svg>
          brennan@larkstone-partners.com.au
        </li>
        <li class="contact__item">
          <svg class="contact__icon" viewBox="0 0 10 10" aria-hidden="true"><circle cx="5" cy="5" r="4" fill="none" stroke="var(--accent-yellow)" stroke-width="1"/><ellipse cx="5" cy="5" rx="1.8" ry="4" fill="none" stroke="var(--accent-yellow)" stroke-width="0.8"/><path d="M1 5 H9" stroke="var(--accent-yellow)" stroke-width="0.8"/></svg>
          www.larkstone-partners.com.au
        </li>
      </ul>
    </div>
  </section>

</main>
</body>
</html>
```